The Builders Group for Structures and Shelter Systems

The Brochure need to have all the company information and our three products with features and specifications.

1- Sandline Cube
2- Sandline Ridge
3- Sandline Vault

We build movable fast build up houses, we are creative and innovative in making designs. we are ECO friendly to the environment. we have an experienced team. We work in Saudi Arabia. we build large number of luxurious houses for hotels and resorts.

Target Market(s)

Hospitality, Tourism, Real State, Saudi Arabia, Mega projects,

Industry/Entity Type

Residential Construction

Font styles to use
Serif

Colors

Designer to choose colors to be used in the design.

Requirements
Must have
• who we are, what we do vision mission values, Products part. Features part, pictures ,our clients our team contact us. Slogan
Nice to have
• it will be decided later
Should not have
• It will be deiced later

```html
<!DOCTYPE html>
<html lang="en">
<head>
<meta charset="utf-8">
<title>Sandline Cube Brochure – Pages 5 and 6</title>
<link rel="stylesheet" href="https://fonts.googleapis.com/css2?family=Montserrat:wght@400;500;600;700&display=swap">
<style>
  :root {
    --canvas: #ecebe8;
    --paper: #ffffff;
    --paper-edge: #f2f3f4;
    --ink: #1f2a33;
    --ink-soft: #3b4650;
    --navy-glass: rgba(44, 60, 76, 0.82);
    --rule: rgba(255, 255, 255, 0.7);
    --brand-teal: #3f9aa0;
    --dot-line: #9aa3ab;
    --sky-top: #6f8294;
    --sky-mid: #b9b6b4;
    --dusk: #2c3238;
    --deck: #7a5132;
    --deck-dark: #3d2616;
  }

  * { box-sizing: border-box; margin: 0; padding: 0; }

  html, body {
    width: 1200px;
    height: 900px;
    overflow: hidden;
    background: var(--canvas);
    font-family: "Montserrat", sans-serif;
    color: var(--ink);
  }

  .spread {
    position: absolute;
    left: 20px;
    top: 232px;
    width: 1160px;
    height: 437px;
    display: flex;
    box-shadow: 0 10px 30px rgba(0, 0, 0, 0.18);
  }

  /* ---------- Page 5: hero ---------- */
  .hero {
    position: relative;
    width: 782px;
    height: 100%;
    overflow: hidden;
  }

  .hero-photo {
    position: absolute;
    inset: 0;
    background:
      linear-gradient(180deg, transparent 62%, var(--deck) 80%, var(--deck-dark) 100%),
      linear-gradient(90deg, rgba(30, 36, 42, 0.55) 0%, transparent 30%, transparent 45%, var(--dusk) 62%, #1c2024 100%),
      linear-gradient(180deg, var(--sky-top) 0%, var(--sky-mid) 32%, #5b5e60 55%, var(--dusk) 70%);
  }

  .intro-panel {
    position: absolute;
    left: 0;
    top: 50px;
    width: 324px;
    height: 339px;
    background: var(--navy-glass);
    color: #fff;
    padding: 64px 26px 0 26px;
  }

  .intro-title {
    font-size: 17px;
    font-weight: 400;
    letter-spacing: 2.2px;
    line-height: 1.3;
    text-transform: uppercase;
  }

  .intro-title strong { font-weight: 600; }

  .intro-rule {
    width: 270px;
    height: 1px;
    background: var(--rule);
    margin: 7px 0 12px;
  }

  .intro-heading {
    font-size: 14.5px;
    font-weight: 500;
    margin-bottom: 18px;
  }

  .intro-body {
    font-size: 7.6px;
    line-height: 1.42;
    color: rgba(255, 255, 255, 0.92);
  }

  .intro-body + .intro-body { margin-top: 10px; }

  .brand-tag {
    display: flex;
    align-items: center;
    gap: 4px;
    font-size: 5.5px;
    font-weight: 500;
    color: var(--brand-teal);
  }

  .brand-tag .brand-dot {
    width: 9px;
    height: 9px;
    border-radius: 50%;
    background: var(--brand-teal);
  }

  .hero .brand-tag {
    position: absolute;
    left: 30px;
    bottom: 20px;
  }

  /* ---------- Page 6: features ---------- */
  .features {
    position: relative;
    flex: 1;
    height: 100%;
    background: linear-gradient(90deg, var(--paper) 0%, var(--paper) 85%, var(--paper-edge) 100%);
    padding: 64px 20px 0 19px;
  }

  .features-title {
    font-size: 13.5px;
    font-weight: 700;
    color: var(--ink);
    margin-bottom: 22px;
  }

  .feature-list {
    position: relative;
    list-style: none;
  }

  .feature-list::before {
    content: "";
    position: absolute;
    left: 14px;
    top: 14px;
    bottom: 16px;
    border-left: 1px dotted var(--dot-line);
  }

  .feature {
    position: relative;
    display: flex;
    gap: 10px;
    margin-bottom: 11px;
  }

  .feature-icon {
    flex: 0 0 28px;
    height: 28px;
    background: var(--paper);
    position: relative;
    z-index: 1;
  }

  .feature-icon svg { width: 28px; height: 28px; display: block; }

  .feature-name {
    font-size: 8.8px;
    font-weight: 700;
    color: var(--ink);
    margin-bottom: 3px;
  }

  .feature-text {
    font-size: 7.6px;
    line-height: 1.35;
    color: var(--ink-soft);
  }

  .features .brand-tag {
    position: absolute;
    right: 24px;
    bottom: 18px;
  }
</style>
</head>
<body>
  <main class="spread">
    <section class="hero">
      <div class="hero-photo" role="img" aria-label="Photograph of a black shipping container home at dusk with wide glass doors, a lit timber canopy and a wooden deck with patio chairs and an umbrella, framed by trees"></div>

      <div class="intro-panel">
        <h1 class="intro-title"><strong>Sandline Cube-</strong> the most luxurious unit</h1>
        <div class="intro-rule"></div>
        <h2 class="intro-heading">Why Shipping Containers?</h2>
        <p class="intro-body">A shipping container home makes the construction process much simpler and more efficient than ever before. So why spend months building when it could be weeks? Imagine them as life-size BLOKKO blocks and you will start to see the vast possibilities and opportunities.</p>
        <p class="intro-body">Build a single level or multi-levels building. Place one in your backyard and then 10 years later move it somewhere new. When it comes to construction methods and building materials there are few alternatives that are as durable, portable and sustainable.</p>
      </div>

      <div class="brand-tag"><span class="brand-dot"></span>The Builders Group</div>
    </section>

    <section class="features">
      <h2 class="features-title">Why Sandline Cube?</h2>
      <ol class="feature-list">
        <li class="feature">
          <span class="feature-icon">
            <svg viewBox="0 0 28 28" fill="none" stroke="var(--ink)" stroke-width="1.8" stroke-linejoin="round" stroke-linecap="round">
              <path d="M14 3 L23 6.5 V13 C23 19 19 23 14 25 C9 23 5 19 5 13 V6.5 Z"/>
              <path d="M9.5 14 L12.8 17.2 L18.8 10.8"/>
            </svg>
          </span>
          <div>
            <h3 class="feature-name">1. DURABILITY</h3>
            <p class="feature-text">A Sandline Cube unit is built with an engineered commercial grade steel frame - Providing superior strength and a longer lifespan compared to traditional residential building materials.</p>
          </div>
        </li>
        <li class="feature">
          <span class="feature-icon">
            <svg viewBox="0 0 28 28" fill="none" stroke="var(--ink)" stroke-width="1.5" stroke-linejoin="round">
              <path d="M12.3 3h3.4l.6 3.1 2.2 1 2.7-1.7 2.4 2.4-1.7 2.7 1 2.2 3.1.6v3.4l-3.1.6-1 2.2 1.7 2.7-2.4 2.4-2.7-1.7-2.2 1-.6 3.1h-3.4l-.6-3.1-2.2-1-2.7 1.7-2.4-2.4 1.7-2.7-1-2.2L3 15.7v-3.4l3.1-.6 1-2.2-1.7-2.7 2.4-2.4 2.7 1.7 2.2-1z"/>
              <circle cx="14" cy="14" r="4"/>
            </svg>
          </span>
          <div>
            <h3 class="feature-name">2. STREAMLINED</h3>
            <p class="feature-text">Simultaneous site development and building construction at the Sandline Cube facility. Reducing project schedules by 30-50%.</p>
          </div>
        </li>
        <li class="feature">
          <span class="feature-icon">
            <svg viewBox="0 0 28 28">
              <path d="M7 23 C4 15 9 6 22 4 C23 15 17 23 7 23 Z" fill="var(--ink)"/>
              <path d="M7 23 C11 17 14 13 18 9" stroke="#fff" stroke-width="1.3" fill="none" stroke-linecap="round"/>
            </svg>
          </span>
          <div>
            <h3 class="feature-name">3. ENVIRONMENTAL</h3>
            <p class="feature-text">Sandline Cube is an environmental housing unit that does not need to have a foundation on the ground.</p>
          </div>
        </li>
        <li class="feature">
          <span class="feature-icon">
            <svg viewBox="0 0 28 28" fill="none" stroke="var(--ink)" stroke-width="1.8" stroke-linecap="round">
              <path d="M5 19 A10 10 0 1 1 23 19"/>
              <path d="M14 15 L19 9"/>
              <circle cx="14" cy="15" r="1.6" fill="var(--ink)"/>
              <path d="M9 23 H19"/>
            </svg>
          </span>
          <div>
            <h3 class="feature-name">4. EFFICIENCY</h3>
            <p class="feature-text">Every Sandline Cube is equipped with proven all electric systems which allows for renewable energy sources to offset some or all of the energy usage.</p>
          </div>
        </li>
        <li class="feature">
          <span class="feature-icon">
            <svg viewBox="0 0 28 28" fill="var(--ink)">
              <rect x="3" y="10" width="2" height="8"/>
              <rect x="7" y="10" width="2" height="8"/>
              <rect x="11" y="10" width="3" height="8"/>
              <path d="M16 7 L25 14 L16 21 Z"/>
            </svg>
          </span>
          <div>
            <h3 class="feature-name">5. MOVABLE</h3>
            <p class="feature-text">Sandline Cube unit is a movable unit and can be easily transfered from location to another.</p>
          </div>
        </li>
      </ol>

      <div class="brand-tag"><span class="brand-dot"></span>The Builders Group</div>
    </section>
  </main>
</body>
</html>
```